Executive recruiting firm in need of business card design

Executive recruiting firm looking for a sleek, classy and modern business card design; card itself will be square shape, rounded edges and soft touch paper, our colors are dark blues in the navy color scale, silvers and grays. Reference our website for a better idea of our company's feel and goals at Tarvex-Up.com - our company message is "Employee Engagement Begins at Recruitment" this should be on the card

```html
<!DOCTYPE html>
<html lang="en">
<head>
<meta charset="utf-8">
<title>Tarvex Up — Business Card</title>
<link rel="stylesheet" href="https://fonts.googleapis.com/css2?family=Open+Sans:wght@300;400;700&display=swap">
<style>
  :root {
    --navy: #1b1f6e;
    --navy-deep: #12154f;
    --white: #ffffff;
    --ink: #1b1f6e;
    --backdrop: #e9eaee;
  }
  * { margin: 0; padding: 0; box-sizing: border-box; }
  html, body { width: 1200px; height: 840px; overflow: hidden; }
  body {
    background: var(--backdrop);
    font-family: "Open Sans", Arial, sans-serif;
    display: flex;
    flex-direction: column;
    align-items: center;
    justify-content: center;
    gap: 40px;
  }
  .card {
    position: relative;
    width: 640px;
    height: 366px;
    border-radius: 6px;
    overflow: hidden;
    box-shadow: 0 6px 18px rgba(18, 21, 79, 0.18);
  }
  .brand-name {
    position: absolute;
    left: 0; right: 0;
    text-align: center;
    font-weight: 300;
    font-size: 44px;
    letter-spacing: 6px;
    line-height: 1;
    white-space: nowrap;
  }
  .card-front {
    background: linear-gradient(135deg, var(--navy) 0%, var(--navy-deep) 100%);
    color: var(--white);
  }
  .card-front .brand-name { top: 128px; }
  .message {
    position: absolute;
    left: 0; right: 0; bottom: 64px;
    text-align: center;
    font-size: 15px;
    font-weight: 400;
  }
  .card-back { background: var(--navy); }
  .card-back .wave { position: absolute; inset: 0; width: 100%; height: 100%; }
  .card-back .brand-name { top: 100px; color: var(--ink); }
  .contact {
    position: absolute;
    right: 36px;
    bottom: 24px;
    width: 380px;
    text-align: center;
    color: var(--white);
    font-size: 12.5px;
    line-height: 1.55;
  }
  .contact-name { font-weight: 700; }
</style>
</head>
<body>
  <section class="card card-front">
    <span class="brand-name">TARVEX UP</span>
    <p class="message">Employee Engagement Begins at Recruitment</p>
  </section>

  <section class="card card-back">
    <svg class="wave" viewBox="0 0 640 366" preserveAspectRatio="none">
      <path d="M0 0 H640 V60 C570 170 430 228 280 228 C160 228 70 210 0 190 Z" fill="#ffffff"/>
    </svg>
    <span class="brand-name">TARVEX UP</span>
    <div class="contact">
      <p><span class="contact-name">DANIEL REYES</span> - CEO/FOUNDER</p>
      <p>240 West Harbor Ave., Lakeview, CA</p>
      <p>(P) 555 014 2738 (M) 555 019 6364 (F) 555 017 1940</p>
      <p>(E) daniel@tarvex-up.com (W) www.tarvex-up.com</p>
    </div>
  </section>
</body>
</html>
```